QVR business card

Need a business card for a company that provides instructional design and elearning development services. The website is here: http://quorvane.studio/

I'm attaching a current logo, as well as the old business card design. While I like to keep it clean, the old design is too simplistic for my liking. The only idea I want to reuse from the old design is placing industry jargon on the back of the card, just need a better way to present it. But if you have other ideas for the back--feel free to experiment.

Please use the colors complementary to the color we have on the website. Thank you!

```html
<!DOCTYPE html>
<html lang="en">
<head>
<meta charset="utf-8">
<title>QVR business card</title>
<link rel="stylesheet" href="https://fonts.googleapis.com/css2?family=Jost:wght@500;600&family=Lato:wght@400;700&family=Oswald:wght@600&display=swap">
<style>
  :root {
    --teal: #14b2aa;
    --gold: #d8cc8f;
    --card-back: #2a2b2e;
    --muted: #8a8d92;
    --paper: #ffffff;
    --page: #ececec;
  }
  html, body {
    margin: 0;
    width: 1138px;
    height: 1200px;
    overflow: hidden;
    background: var(--page);
  }
  .canvas { position: relative; width: 1138px; height: 1200px; }

  .card {
    position: absolute;
    border-radius: 14px;
    overflow: hidden;
    box-shadow: 0 4px 14px rgba(0,0,0,.18);
  }
  .card--front { left: 218px; top: 198px; width: 671px; height: 384px; background: var(--paper); }
  .card--back  { left: 216px; top: 618px; width: 670px; height: 380px; background: var(--card-back); }

  .brand {
    position: absolute; left: 38px; top: 58px;
    display: flex; align-items: center; gap: 14px;
    font-family: "Lato", sans-serif; font-weight: 700;
    font-size: 58px; letter-spacing: 4px; color: var(--teal);
  }
  .brand__dot { width: 26px; height: 26px; border-radius: 50%; background: var(--gold); }

  .holder {
    position: absolute; left: 35px; top: 198px; margin: 0;
    font-family: "Lato", sans-serif; font-weight: 700;
    font-size: 21px; color: var(--teal);
  }

  .contact-band {
    position: absolute; left: 0; top: 244px; width: 530px; height: 100px;
    background: var(--teal);
    clip-path: polygon(0 0, 100% 0, 92% 100%, 0 100%);
  }
  .contact {
    position: absolute; left: 36px; top: 262px; margin: 0; padding: 0; list-style: none;
    font-family: "Lato", sans-serif; font-size: 18px; color: var(--paper);
  }
  .contact li { display: flex; align-items: center; gap: 9px; height: 23px; }
  .contact svg { width: 15px; height: 15px; flex: none; }

  .back__kicker {
    position: absolute; left: 44px; top: 38px; margin: 0;
    font-family: "Lato", sans-serif; font-weight: 700; font-size: 15px;
    letter-spacing: 3px; color: var(--gold);
  }
  .back__headline {
    position: absolute; left: 44px; top: 60px; margin: 0;
    font-family: "Oswald", sans-serif; font-weight: 600; font-size: 42px;
    line-height: 52px; color: var(--paper);
  }
  .back__rule {
    position: absolute; left: 44px; top: 124px; width: 64px; height: 4px; background: var(--teal);
  }
  .services {
    position: absolute; left: 44px; top: 150px; width: 590px;
    margin: 0; padding: 0; list-style: none;
    display: grid; grid-template-columns: 1fr 1fr; column-gap: 24px;
    font-family: "Jost", sans-serif; font-weight: 500; font-size: 20px;
    line-height: 32px; color: var(--teal);
  }
  .services li { display: flex; align-items: center; gap: 10px; white-space: nowrap; }
  .services li::before {
    content: ""; width: 6px; height: 6px; border-radius: 50%; background: var(--muted); flex: none;
  }
</style>
</head>
<body>
<main class="canvas">

  <section class="card card--front" aria-label="Business card front">
    <div class="brand"><span class="brand__dot"></span>QVR</div>
    <p class="holder">Adrian Velmore</p>
    <div class="contact-band"></div>
    <ul class="contact">
      <li>
        <svg viewBox="0 0 16 16" aria-hidden="true"><path fill="#fff" d="M4 1.5l2.2 3-1.3 1.4c.8 2 2.3 3.6 4.3 4.5l1.4-1.3 3 2.2-1.4 2.7C7 13.7 2.3 9 1.3 3z"/></svg>
        555-013-2847
      </li>
      <li>
        <svg viewBox="0 0 16 16" aria-hidden="true"><rect x="1" y="3" width="14" height="10" fill="#fff"/><path d="M1 3l7 6 7-6" fill="none" stroke="#14b2aa" stroke-width="1.4"/></svg>
        avelmore@quorvane.studio
      </li>
      <li>
        <svg viewBox="0 0 16 16" aria-hidden="true"><g fill="none" stroke="#fff" stroke-width="1.3"><circle cx="8" cy="8" r="6.5"/><ellipse cx="8" cy="8" rx="3" ry="6.5"/><path d="M1.5 8h13M2.5 4.8h11M2.5 11.2h11"/></g></svg>
        www.quorvane.studio
      </li>
    </ul>
  </section>

  <section class="card card--back" aria-label="Business card back">
    <p class="back__kicker">WHAT WE DO</p>
    <h2 class="back__headline">Courses people finish.</h2>
    <div class="back__rule"></div>
    <ul class="services">
      <li>Instructional design</li>
      <li>LMS setup</li>
      <li>Adult learning theory</li>
      <li>SCORM &amp; xAPI</li>
      <li>Blended learning</li>
      <li>HTML5 modules</li>
      <li>Mobile learning</li>
      <li>Gamification</li>
      <li>MOOCs</li>
      <li>Classroom training</li>
    </ul>
  </section>

</main>
</body>
</html>
```